Webdesign für Verkauf von Stoffen
Zielgruppe
Plinzgarne ist schon seit 15 Jahren auf den Märkten unterwegs und verkauft seine hochwertigen Stoffe vor Ort. Nun muss die Webseite ein neuen Look bekommen, sie sollte modern und locker wirken. Die Webseite ist eher für Privatkunden und hat jetzt noch keine Shop Möglichkeit, die wird aber intrigiert mit einzelnen Produkten.
Aufgabenstellung
Logo gibt es noch nicht, soll erstmal nur in Schriftform bleiben, ansonsten gibt es keine explizierten Vorgaben

```html
<!DOCTYPE html>
<html lang="de">
<head>
<meta charset="utf-8">
<title>Plinzgarne – Feiner Zwirn</title>
<link href="https://fonts.googleapis.com/css2?family=Montserrat:wght@400;500;600;700&display=swap" rel="stylesheet">
<style>
:root{
  --ink:#0d0f0e;
  --white:#ffffff;
  --accent:#e2611f;
  --line:#f0b58a;
  --note:#e33fd0;
  --frame:#555555;
  --veil:rgba(225,225,225,.82);
}
*{margin:0;padding:0;box-sizing:border-box}
html,body{width:1200px;height:2285px;overflow:hidden;background:var(--white)}
body{position:relative;font-family:'Montserrat',sans-serif;color:var(--ink)}
.abs{position:absolute}
.center{text-align:center}
.site-header{background:var(--ink);height:116px;color:var(--white)}
.zigzag{position:absolute;left:0;display:block}
.brand{font-weight:600;letter-spacing:2px;color:var(--white)}
.tagline{color:var(--white)}
.nav{font-size:8.5px;color:var(--white);font-weight:500}
.nav .current{color:var(--accent)}
.social{width:21px;height:21px;border-radius:50%;background:var(--ink)}
.page-title{font-weight:700;letter-spacing:.5px}
.title-rule{height:1.5px;background:var(--line)}
.intro{font-size:9.6px;line-height:18.7px}
.photo{display:block}
.hero-veil{background:var(--veil)}
.btn{background:var(--ink);color:var(--white);border-radius:4px;display:flex;align-items:center;justify-content:center}
.card{border:1px solid var(--frame);background:var(--white);overflow:hidden}
.card-title{font-weight:700}
.card-text{line-height:18.6px}
.note{color:var(--note);font-size:15px;line-height:21px}
.link-note{z-index:5;pointer-events:none}
.dot{width:11px;height:11px;border-radius:50%;border:1px solid #bbb;background:var(--white)}
.dot.on{background:var(--ink);border-color:var(--ink)}
.site-footer{background:var(--ink);color:var(--white);font-size:8.8px}
</style>
</head>
<body>

<svg width="0" height="0" class="abs" aria-hidden="true">
  <defs>
    <pattern id="teeth-down-black" width="14" height="14" patternUnits="userSpaceOnUse"><path d="M0 0L7 14L14 0Z" fill="#0d0f0e"/></pattern>
    <pattern id="teeth-down-white" width="14" height="12" patternUnits="userSpaceOnUse"><path d="M0 0L14 0L7 12Z" fill="#fff"/></pattern>
    <pattern id="teeth-up-white" width="14" height="12" patternUnits="userSpaceOnUse"><path d="M0 12L7 0L14 12Z" fill="#fff"/></pattern>
    <linearGradient id="g-hero" x1="0" y1="0" x2="1" y2="0"><stop offset="0" stop-color="#c9cbc6"/><stop offset=".25" stop-color="#9a4a36"/><stop offset=".5" stop-color="#b08a6e"/><stop offset=".75" stop-color="#4e6b73"/><stop offset="1" stop-color="#d8d6d2"/></linearGradient>
  </defs>
</svg>

<!-- ===== Desktop layout ===== -->
<header class="site-header abs" style="left:0;top:0;width:996px">
  <div class="brand abs center" style="left:0;width:1036px;top:28px;font-size:30px">PLINZGARNE</div>
  <div class="tagline abs center" style="left:0;width:1036px;top:70px;font-size:11.5px">FEINER ZWIRN</div>
  <nav class="nav abs center" style="left:0;width:1040px;top:97px"><span class="current">HOME</span> | PORTFOLIO | ÜBER MICH | KONTAKT</nav>
</header>
<svg class="zigzag" style="top:116px" width="996" height="14"><rect width="996" height="14" fill="url(#teeth-down-black)"/></svg>

<div class="social abs" role="img" aria-label="Soziales Netzwerk" style="left:961px;top:157px"></div>
<div class="social abs" role="img" aria-label="Soziales Netzwerk" style="left:961px;top:187px"></div>

<h1 class="page-title abs center" style="left:0;width:996px;top:185px;font-size:16.5px">PLINZGARNE - FEINER ZWIRN</h1>
<div class="title-rule abs" style="left:350px;top:212px;width:295px"></div>
<p class="intro abs center" style="left:0;width:996px;top:225px">Ich biete derzeit auf dem Stoffmeile Nord deutschlandweit meine Stoffe an.<br>Der Onlineshop befindet sich momentan noch in der Aufbauphase und ist voraussichtlich<br>ab Mitte 2022 für Euch zugänglich.</p>

<section class="hero abs" style="left:0;top:321px;width:996px;height:485px">
  <svg class="photo" width="996" height="485" role="img" aria-label="Foto: Schneiderin mit Maßband vor einer Kleiderstange mit Stoffen"><rect width="996" height="485" fill="url(#g-hero)"/><rect width="996" height="12" fill="url(#teeth-down-white)"/><rect y="473" width="996" height="12" fill="url(#teeth-up-white)"/></svg>
  <div class="hero-veil abs" style="left:183px;top:302px;width:647px;height:124px"></div>
  <p class="abs center" style="left:183px;width:647px;top:314px;font-size:16.5px;line-height:22px">Eleganz kommt nie aus der Mode:<br>Gobelin / Canvas / Linen / Sweat / Jersey / Musselin uvm.</p>
  <a class="btn abs" style="left:442px;top:374px;width:110px;height:33px;font-size:16.5px">Zum Shop</a>
</section>

<article class="card abs" style="left:187px;top:887px;width:294px;height:394px">
  <div class="photo" role="img" aria-label="Foto: Sweatstoff in Grau und Weiß" style="height:195px;background:linear-gradient(135deg,#f2f2f1,#cfcdca 55%,#e9e8e6)"></div>
  <h2 class="card-title abs" style="left:33px;top:247px;font-size:16.5px">Sweat Melange</h2>
  <p class="card-text abs" style="left:33px;top:270px;font-size:9.6px">in einer großen Farbauswahl. Von gedeckten<br>Farbtönen für die Lounge-Wear bis zu kräftigen<br>Faben für den Eye-Catcher.</p>
  <a class="btn abs" style="left:30px;top:338px;width:149px;height:33px;font-size:16.5px">jetzt anschauen</a>
</article>
<article class="card abs" style="left:516px;top:887px;width:294px;height:394px">
  <div class="photo" role="img" aria-label="Foto: gefaltete Musselinstoffe in Rosé, Rot und Grün" style="height:197px;background:linear-gradient(180deg,#c79686,#d79aa7 30%,#9a2a40 55%,#7fa07a 80%,#5e4a3c)"></div>
  <h2 class="card-title abs" style="left:21px;top:244px;font-size:16.5px">Bio Musselin</h2>
  <p class="card-text abs" style="left:21px;top:267px;font-size:9.6px">in einer großen Farbauswahl. Von zarten Rosé bis zu<br>kräftigem Tannengrün.</p>
</article>
<article class="card abs" style="left:187px;top:1321px;width:294px;height:394px">
  <div class="photo" role="img" aria-label="Foto: Leinenstoffrollen in Grüntönen" style="height:197px;background:linear-gradient(90deg,#8c9a8c,#4f8a6a 35%,#a9b8ad 60%,#c4d6cc)"></div>
  <h2 class="card-title abs" style="left:33px;top:258px;font-size:16.5px">Linen / Viskose</h2>
  <p class="card-text abs" style="left:33px;top:281px;font-size:9.6px">in großen Farb- und Musterauswahl, von Kinder-<br>stoffen bis hin zu Blusenstoff</p>
</article>
<article class="card abs" style="left:516px;top:1321px;width:294px;height:394px">
  <div class="photo" role="img" aria-label="Foto: Leinenstoffe in Regenbogenfarben" style="height:197px;background:linear-gradient(90deg,#4a8fd0,#3a6fc4 20%,#cfc48c 40%,#b0704a 55%,#5a2a3a 70%,#d42a40 88%,#c63a4a)"></div>
  <h2 class="card-title abs" style="left:31px;top:258px;font-size:16.5px">Washed Linen</h2>
  <p class="card-text abs" style="left:31px;top:281px;font-size:9.6px">in allen Farben des Regenbogens. Hellblau, Violett,<br>Dunkelrot, Orange, Pink, ...</p>
</article>

<svg class="link-note abs" style="left:0;top:0" width="996" height="1260" aria-hidden="true"><polyline points="552,724 692,839 555,1060 389,1246" fill="none" stroke="#e33fd0" stroke-width=".8"/></svg>
<p class="note abs" style="left:708px;top:823px">sobald Shop aufgebaut:<br>verlinkung</p>

<p class="note abs" style="left:800px;top:1740px">slider</p>
<section class="abs" style="left:0;top:1763px;width:996px;height:339px">
  <div class="photo" role="img" aria-label="Foto: geblümter Stoff mit Maßband" style="height:339px;background:linear-gradient(135deg,#e8c9c4,#d9668e 35%,#e9d36a 55%,#d98aa6 70%,#28506e)"></div>
  <div class="dot abs" style="left:476px;top:311px"></div>
  <div class="dot on abs" style="left:494px;top:311px"></div>
  <div class="dot abs" style="left:512px;top:311px"></div>
</section>
<footer class="site-footer abs center" style="left:0;top:2102px;width:996px;height:52px;padding-top:22px">Impressum | Datenschutz | Cookie-Einstellungen</footer>

<!-- ===== Mobile layout ===== -->
<header class="site-header abs" style="left:1034px;top:0;width:166px">
  <div class="brand abs center" style="left:0;width:176px;top:32px;font-size:17px;letter-spacing:1px">PLINZGARNE</div>
  <div class="tagline abs center" style="left:0;width:176px;top:64px;font-size:7.5px">FEINER ZWIRN</div>
  <svg class="abs" style="left:79px;top:87px" width="22" height="22" role="img" aria-label="Menü"><circle cx="11" cy="11" r="10" fill="none" stroke="#fff" stroke-width="1.2"/><path d="M6 8h10M6 11h10M6 14h7" stroke="#fff" stroke-width="1.4"/></svg>
</header>
<svg class="zigzag" style="left:1034px;top:116px" width="166" height="14"><rect width="166" height="14" fill="url(#teeth-down-black)"/></svg>

<h1 class="page-title abs center" style="left:1034px;width:166px;top:167px;font-size:15px;line-height:19px">PLINZGARNE -<br>FEINER ZWIRN</h1>
<div class="title-rule abs" style="left:1065px;top:213px;width:105px"></div>
<p class="intro abs center" style="left:1034px;width:166px;top:225px;font-size:9.4px">Ich biete derzeit auf dem Stoff-<br>meile Nord deutschlandweit<br>meine Stoffe an.<br>Der Onlineshop befindet sich<br>momentan noch in der Aufbau-<br>phase und ist voraussichtlich<br>ab Mitte 2022 für Euch</p>
<div class="social abs" role="img" aria-label="Soziales Netzwerk" style="left:1093px;top:417px"></div>
<div class="social abs" role="img" aria-label="Soziales Netzwerk" style="left:1125px;top:417px"></div>

<section class="abs" style="left:1034px;top:458px;width:166px;height:259px">
  <svg class="photo" width="166" height="259" role="img" aria-label="Foto: Schneiderin mit Maßband vor Stoffen"><rect width="166" height="259" fill="url(#g-hero)"/><rect width="166" height="12" fill="url(#teeth-down-white)"/><rect y="247" width="166" height="12" fill="url(#teeth-up-white)"/></svg>
  <div class="hero-veil abs" style="left:0;top:130px;width:166px;height:102px"></div>
  <p class="abs center" style="left:0;width:166px;top:154px;font-size:8.2px;line-height:12.5px">Eleganz kommt nie aus der Mode:<br>Gobelin / Canvas / Linen / Sweat /<br>Jersey / Musselin uvm.</p>
  <a class="btn abs" style="left:49px;top:199px;width:75px;height:21px;font-size:8.5px">Zum Shop</a>
</section>

<article class="card abs" style="left:1043px;top:739px;width:148px;height:249px">
  <div class="photo" role="img" aria-label="Foto: Sweatstoff in Grau und Weiß" style="height:100px;background:linear-gradient(135deg,#f2f2f1,#cfcdca 55%,#e9e8e6)"></div>
  <h2 class="card-title abs" style="left:5px;top:104px;font-size:15.5px">Sweat Melange</h2>
  <p class="card-text abs" style="left:5px;top:127px;font-size:8.4px">in einer großen Farbauswahl.<br>Von gedeckten Farbtönen für die<br>Lounge-Wear bis zu kräftigen<br>Faben für den Eye-Catcher.</p>
  <a class="btn abs" style="left:5px;top:209px;width:102px;height:28px;font-size:9.5px">jetzt anschauen</a>
</article>
<article class="card abs" style="left:1041px;top:1001px;width:150px;height:221px">
  <div class="photo" role="img" aria-label="Foto: gefaltete Musselinstoffe" style="height:100px;background:linear-gradient(180deg,#c79686,#d79aa7 30%,#9a2a40 55%,#7fa07a 80%,#5e4a3c)"></div>
  <h2 class="card-title abs" style="left:7px;top:110px;font-size:15.5px">Bio Musselin</h2>
  <p class="card-text abs" style="left:7px;top:132px;font-size:8.4px">in einer großen Farbauswahl.<br>Von zarten Rosé bis zu<br>kräftigem Tannengrün.</p>
</article>
<article class="card abs" style="left:1040px;top:1236px;width:150px;height:213px">
  <div class="photo" role="img" aria-label="Foto: Leinenstoffrollen in Grüntönen" style="height:103px;background:linear-gradient(90deg,#8c9a8c,#4f8a6a 35%,#a9b8ad 60%,#c4d6cc)"></div>
  <h2 class="card-title abs" style="left:6px;top:113px;font-size:15.5px">Linen / Viskose</h2>
  <p class="card-text abs" style="left:6px;top:136px;font-size:8.4px">in großen Farb- und Muster-<br>auswahl, von Kinder-<br>stoffen bis hin zu Blusenstoff</p>
</article>
<article class="card abs" style="left:1041px;top:1466px;width:149px;height:257px">
  <div class="photo" role="img" aria-label="Foto: Leinenstoffe in Regenbogenfarben" style="height:46px;background:linear-gradient(90deg,#4a8fd0,#3a6fc4 20%,#cfc48c 40%,#b0704a 55%,#5a2a3a 70%,#d42a40 88%,#c63a4a)"></div>
  <h2 class="card-title abs" style="left:5px;top:130px;font-size:15.5px">Washed Linen</h2>
  <p class="card-text abs" style="left:5px;top:153px;font-size:8.2px">in allen Farben des Regenbogens.<br>Hellblau, Violett,<br>Dunkelrot, Orange, Pink, ...</p>
</article>

<section class="abs" style="left:1034px;top:1832px;width:166px;height:340px">
  <div class="photo" role="img" aria-label="Foto: geblümter Stoff mit Maßband" style="height:340px;background:linear-gradient(160deg,#e8c9c4,#d9668e 35%,#e9d36a 50%,#d98aa6 62%,#28506e 85%)"></div>
  <div class="dot abs" style="left:67px;top:237px"></div>
  <div class="dot on abs" style="left:85px;top:237px"></div>
  <div class="dot abs" style="left:103px;top:237px"></div>
</section>
<footer class="site-footer abs center" style="left:1034px;top:2172px;width:166px;height:113px;padding-top:28px;line-height:21.5px">Impressum<br>Datenschutz<br>Cookie-Einstellungen</footer>

</body>
</html>
```